Redesign of business card for Cedar Ridge Mechanical

We are looking for a new design for our business cards for Cedar Ridge Mechanical. We are a plumbing & HVAC construction company, operating on the West Coast of Canada and USA. Logo attached.
Industry/Entity Type
Construction - Plumbing & HVAC
Contact Information for Business Card
Name, address, phone numbers, email, website address
Look and feel
Each slider illustrates characteristics of the customer's brand and the style your logo design should communicate.

```html
<!DOCTYPE html>
<html lang="en">
<head>
<meta charset="utf-8">
<title>Cedar Ridge Mechanical – Business Card</title>
<link href="https://fonts.googleapis.com/css2?family=Montserrat:wght@400;700&display=swap" rel="stylesheet">
<style>
  :root {
    --ink: #0b0b0b;
    --paper: #ffffff;
    --stone: #7d7d7d;
    --muted: #444444;
    --backdrop: #2b2b2d;
  }
  html, body {
    margin: 0;
    padding: 0;
    width: 1200px;
    height: 913px;
    overflow: hidden;
    background: var(--backdrop);
    font-family: "Montserrat", Arial, sans-serif;
  }
  .canvas {
    position: relative;
    width: 1200px;
    height: 913px;
  }
  .card {
    position: absolute;
    width: 580px;
    height: 330px;
    border-radius: 22px;
    background: var(--paper);
    overflow: hidden;
  }
  .card--front { left: 70px; top: 90px; }
  .card--back  { left: 550px; top: 490px; }

  .brand {
    display: flex;
    align-items: center;
    gap: 14px;
    font-weight: 700;
    text-transform: uppercase;
    letter-spacing: 0.04em;
    line-height: 1.1;
  }
  .brand__mark {
    flex: none;
    border: 6px solid currentColor;
    box-sizing: border-box;
  }
  .card--front .brand {
    position: absolute;
    left: 0; right: 0; top: 0; bottom: 0;
    justify-content: center;
    color: var(--ink);
    font-size: 28px;
  }
  .card--front .brand__mark { width: 60px; height: 60px; }

  .card__waves {
    position: absolute;
    inset: 0;
  }
  .card--back .brand {
    position: absolute;
    right: 24px;
    top: 24px;
    color: var(--paper);
    font-size: 15px;
    gap: 10px;
  }
  .card--back .brand__mark { width: 34px; height: 34px; border-width: 4px; }

  .holder {
    position: absolute;
    left: 36px;
    top: 188px;
  }
  .holder__name {
    margin: 0;
    font-size: 22px;
    font-weight: 700;
    color: var(--ink);
    letter-spacing: 0.02em;
  }
  .holder__role {
    margin: 2px 0 0;
    font-size: 13px;
    color: var(--muted);
  }
  .contact {
    position: absolute;
    left: 36px;
    top: 250px;
    margin: 0;
    padding: 0;
    list-style: none;
    font-size: 14px;
    color: var(--ink);
  }
  .contact li {
    display: flex;
    align-items: center;
    gap: 8px;
    height: 22px;
  }
  .contact svg { width: 13px; height: 13px; }
  .address {
    position: absolute;
    right: 28px;
    top: 150px;
    margin: 0;
    text-align: right;
    font-style: normal;
    font-size: 14px;
    line-height: 1.5;
    color: var(--muted);
  }
</style>
</head>
<body>
<main class="canvas">

  <section class="card card--front" aria-label="Card front">
    <div class="brand">
      <span class="brand__mark"></span>
      <span>Cedar Ridge Mechanical</span>
    </div>
  </section>

  <section class="card card--back" aria-label="Card back">
    <svg class="card__waves" viewBox="0 0 580 330" preserveAspectRatio="none" aria-hidden="true">
      <path d="M580 60 C560 110 500 120 420 118 C340 116 260 114 200 117 C280 118 360 125 430 132 C510 138 570 125 580 95 Z" fill="var(--stone)"/>
      <path d="M0 0 H580 V60 C560 110 500 120 420 118 C300 115 180 110 90 130 C50 140 20 155 0 175 Z" fill="var(--ink)"/>
      <path d="M210 112 C130 114 70 127 30 158 C80 136 140 122 220 116 Z" fill="var(--paper)"/>
    </svg>

    <div class="brand">
      <span class="brand__mark"></span>
      <span>Cedar Ridge Mechanical</span>
    </div>

    <address class="address">Your address, City<br>State, Zip 1234</address>

    <div class="holder">
      <h2 class="holder__name">DANIEL HAYES</h2>
      <p class="holder__role">Managing Director</p>
    </div>

    <ul class="contact">
      <li>
        <svg viewBox="0 0 16 16" aria-hidden="true"><path d="M3 1 L6 1 L7 5 L5 6.5 C6 9 7 10 9.5 11 L11 9 L15 10 L15 13 C15 14 14 15 13 15 C7 15 1 9 1 3 C1 2 2 1 3 1 Z" fill="var(--ink)"/></svg>
        <span>123 456 789</span>
      </li>
      <li>
        <svg viewBox="0 0 16 16" aria-hidden="true"><rect x="1" y="3" width="14" height="10" rx="1.5" fill="var(--ink)"/><path d="M2 4 L8 9 L14 4" stroke="var(--paper)" stroke-width="1.4" fill="none"/></svg>
        <span>info@yourgmail.com</span>
      </li>
      <li>
        <svg viewBox="0 0 16 16" aria-hidden="true"><circle cx="8" cy="8" r="7" fill="var(--ink)"/><path d="M1 8 H15 M8 1 C5 4 5 12 8 15 M8 1 C11 4 11 12 8 15" stroke="var(--paper)" stroke-width="1" fill="none"/></svg>
        <span>www.yourwebsite.com</span>
      </li>
    </ul>
  </section>

</main>
</body>
</html>
```